BUSINESS CARD FOR GUITAR SCHOOL

I would like to design a business card for my Guitar Music School. The school is called "Pluck & Lantern".

The card should be yellow.

Target Market(s)

18-35 years old

Industry/Entity Type

School

Contact Information for Business Card

I would like to design a business card for my Guitar Music School. The school is called "Pluck & Lantern". The card should be yellow.

Card must be consistent with my website design: www.pluckandlantern.com.sg

Requirements
Must have
• 1) Name of Company
• 2) Company Logo
• 3) Name of Employee
• 4) Position of Employee
• 5) Contact Number
• 6) Address
Nice to have
• Creative Design
• Card must be consistent with my website design: www.pluckandlantern.com.sg
Should not have
• Boring Design

```html
<!DOCTYPE html>
<html lang="en">
<head>
<meta charset="utf-8">
<title>Pluck &amp; Lantern – Business Card</title>
<link rel="stylesheet" href="https://fonts.googleapis.com/css2?family=Open+Sans:wght@400;600;800&display=swap">
<style>
  :root {
    --yellow: #f9d80a;
    --yellow-deep: #f2c800;
    --black: #0d0d0d;
    --ink: #141414;
    --white: #ffffff;
    --backdrop: #e9e6e1;
  }
  * { margin: 0; padding: 0; box-sizing: border-box; }
  html, body {
    width: 1200px; height: 913px; overflow: hidden;
    background: var(--backdrop);
    font-family: "Open Sans", Arial, sans-serif;
  }
  .stage { position: relative; width: 1200px; height: 913px; }

  .card {
    position: absolute;
    width: 560px; height: 320px;
    border-radius: 4px;
    overflow: hidden;
    box-shadow: 0 14px 30px rgba(0,0,0,.18);
  }
  .card--front {
    left: 60px; top: 120px;
    background: linear-gradient(135deg, var(--yellow) 0%, var(--yellow-deep) 100%);
    display: flex; align-items: center; justify-content: center;
  }
  .card--back {
    left: 580px; top: 470px;
    background: var(--yellow);
  }

  .brand { color: var(--ink); }
  .brand__name {
    display: flex; align-items: center; gap: 10px;
    font-weight: 800; letter-spacing: -1px; line-height: 1;
    white-space: nowrap;
  }
  .brand__dot {
    width: 0.5em; height: 0.5em; border-radius: 50%;
    background: var(--ink);
  }
  .brand__tagline { font-weight: 600; margin-top: 6px; white-space: nowrap; }

  .card--front .brand { position: relative; margin-top: -10px; }
  .card--front .brand__name { font-size: 46px; }
  .card--front .brand__tagline { font-size: 15px; padding-left: 4px; }

  .card--back .brand { position: absolute; left: 40px; top: 48px; }
  .card--back .brand__name { font-size: 30px; }
  .card--back .brand__tagline { font-size: 11px; padding-left: 2px; }

  .back-panel { position: absolute; inset: 0; }

  .person { position: absolute; left: 40px; bottom: 34px; }
  .person__name { color: var(--yellow); font-weight: 800; font-size: 17px; }
  .person__role { color: var(--white); font-size: 13px; margin-top: 2px; }

  .contact {
    position: absolute; right: 36px; top: 150px;
    color: var(--white); font-size: 12px; line-height: 1.65;
    list-style: none;
  }
  .contact__item { display: flex; align-items: center; gap: 8px; }
  .contact__address { padding-left: 20px; }
  .contact__icon { width: 12px; height: 12px; flex: none; }
</style>
</head>
<body>
<main class="stage">

  <section class="card card--front" aria-label="Business card front">
    <div class="brand">
      <div class="brand__name"><span>Pluck &amp; Lantern</span><span class="brand__dot"></span></div>
      <div class="brand__tagline">Every String Tells a Story Worth Playing</div>
    </div>
  </section>

  <section class="card card--back" aria-label="Business card back">
    <svg class="back-panel" width="560" height="320" viewBox="0 0 560 320" aria-hidden="true">
      <polygon points="0,205 560,80 560,320 0,320" fill="var(--black)"/>
    </svg>

    <div class="brand">
      <div class="brand__name"><span>Pluck &amp; Lantern</span><span class="brand__dot"></span></div>
      <div class="brand__tagline">Every String Tells a Story Worth Playing</div>
    </div>

    <div class="person">
      <div class="person__name">Your Long Name</div>
      <div class="person__role">Managing Director</div>
    </div>

    <ul class="contact">
      <li class="contact__address">27 Keppel Lane Harbour Block<br>C #05-03 Singapore 418822</li>
      <li class="contact__item">
        <svg class="contact__icon" viewBox="0 0 12 12" aria-hidden="true">
          <path d="M2 1h2.5l1 2.5-1.5 1a6 6 0 0 0 3.5 3.5l1-1.5L11 7.5V10a1 1 0 0 1-1 1A9 9 0 0 1 1 2a1 1 0 0 1 1-1z" fill="var(--yellow)"/>
        </svg>
        <span>+65 90417723</span>
      </li>
      <li class="contact__item">
        <svg class="contact__icon" viewBox="0 0 12 12" aria-hidden="true">
          <rect x="1" y="2.5" width="10" height="7" rx="1" fill="var(--yellow)"/>
          <path d="M1.5 3l4.5 3.5L10.5 3" stroke="var(--black)" stroke-width="1" fill="none"/>
        </svg>
        <span>yourname@pluckandlantern.com.sg</span>
      </li>
      <li class="contact__item">
        <svg class="contact__icon" viewBox="0 0 12 12" aria-hidden="true">
          <circle cx="6" cy="6" r="5" fill="var(--yellow)"/>
          <path d="M1 6h10M6 1c2 2 2 8 0 10M6 1c-2 2-2 8 0 10" stroke="var(--black)" stroke-width=".8" fill="none"/>
        </svg>
        <span>www.pluckandlantern.com.sg</span>
      </li>
    </ul>
  </section>

</main>
</body>
</html>
```